New Email Marketing Design Project

I’d like you to make an email template. I’ll be welcoming and on boarding customers via email. And I’d like the branding to stand out. Keep it professional and simple. But be creative.

Design should look amazing on desktop and mobile phones.

Negative white space is ok.

Use stock images

I’ll like to have a spot for a picture of myself so make sure to include a circle where I can show my face so that email viewers will know who is speaking to them.

Target Market(s)

Practice managers, doctors, medical providers

Font styles to use
Sans Serif

Requirements
Must have
• Our Logo, CTA buttons, Same colors as website.
https://www.tarvoclaimservices.com

```html
<!DOCTYPE html>
<html lang="en">
<head>
<meta charset="utf-8">
<title>Tarvo Claim Services – Welcome Email</title>
<link href="https://fonts.googleapis.com/css2?family=Montserrat:wght@300;400;600;700&family=Source+Sans+3:wght@400;600;700&display=swap" rel="stylesheet">
<style>
  :root {
    --brand-blue: #2f77a0;
    --brand-deep: #1f5c85;
    --ink: #1e2a33;
    --muted: #8a8f94;
    --band-dark: #4b4c4e;
    --page-bg: #e6e7e8;
    --white: #ffffff;
  }
  * { box-sizing: border-box; margin: 0; padding: 0; }
  html, body { width: 1200px; height: 1014px; overflow: hidden; }
  body {
    background: var(--page-bg);
    font-family: "Source Sans 3", "Helvetica Neue", Arial, sans-serif;
    color: var(--ink);
  }
  .email {
    position: absolute; left: 260px; top: 0;
    width: 680px; height: 1014px;
    background: var(--white);
  }
  /* Header */
  .header { position: absolute; left: 0; top: 0; width: 680px; height: 50px; display: flex; align-items: center; }
  .brand { display: flex; align-items: center; margin-left: 16px; gap: 14px; }
  .brand-dot { width: 26px; height: 26px; border-radius: 50%; border: 2px solid var(--brand-blue); }
  .brand-name { font-weight: 700; font-size: 15px; color: var(--brand-deep); }
  .helpline { position: absolute; left: 390px; top: 12px; display: flex; align-items: center; gap: 8px; }
  .helpline small { display: block; font-family: "Montserrat", sans-serif; font-size: 7.5px; color: var(--ink); }
  .helpline strong { display: block; font-family: "Montserrat", sans-serif; font-size: 11px; font-weight: 600; letter-spacing: .5px; }
  .cta {
    position: absolute; right: 10px; top: 11px;
    height: 28px; padding: 0 10px;
    display: flex; align-items: center; gap: 6px;
    background: var(--brand-blue); color: var(--white);
    font-family: "Montserrat", sans-serif; font-size: 10px; font-weight: 700;
    text-decoration: none; border-radius: 2px;
  }
  /* Hero */
  .hero { position: absolute; left: 0; top: 50px; width: 680px; height: 411px; overflow: hidden; }
  .hero-photo { position: absolute; inset: 0; background: linear-gradient(120deg, #c9d3da 0%, #eef0f1 45%, #f7f7f6 70%, #d9e3ea 100%); }
  .hero-tint { position: absolute; inset: 0; }
  .hero-title {
    position: absolute; left: 34px; top: 225px;
    font-family: "Montserrat", sans-serif; line-height: 1.05;
  }
  .hero-title .line-one { display: block; font-size: 54px; font-weight: 700; color: var(--white); }
  .hero-title .line-two { display: block; font-size: 54px; font-weight: 400; color: var(--brand-deep); margin-top: 8px; }
  .hero-band { position: absolute; left: 0; top: 461px; width: 680px; height: 39px; background: var(--band-dark); }
  .portrait {
    position: absolute; left: 458px; top: 396px; width: 184px; height: 184px; border-radius: 50%;
    border: 4px solid var(--brand-blue);
    background: radial-gradient(circle at 50% 40%, #dfe6ea 0%, #aebcc6 60%, #7f95a5 100%);
  }
  /* Sections */
  .section-title { position: absolute; left: 42px; font-size: 25px; font-weight: 700; color: var(--brand-deep); }
  .section-text { position: absolute; left: 42px; font-size: 11.5px; line-height: 14px; color: var(--muted); }
  .about-title { top: 540px; }
  .about-text { top: 569px; width: 350px; }
  .services-title { top: 659px; }
  .services-text { top: 688px; width: 590px; }
  .service-row { position: absolute; left: 42px; top: 748px; width: 600px; display: flex; justify-content: space-between; }
  .service { width: 100px; text-align: center; }
  .service svg { display: block; margin: 0 auto 10px; }
  .service p { font-size: 6.5px; line-height: 8px; color: var(--muted); }
  .news-label { position: absolute; left: 42px; top: 838px; font-family: "Montserrat", sans-serif; font-size: 8.5px; font-weight: 600; color: var(--muted); }
  .news-text { position: absolute; left: 42px; top: 856px; width: 590px; font-family: "Montserrat", sans-serif; font-size: 8.6px; font-weight: 600; line-height: 17px; color: #a3a7ab; }
  /* Contact */
  .contact { position: absolute; left: 42px; top: 940px; display: flex; align-items: center; gap: 14px; font-family: "Montserrat", sans-serif; font-size: 6.5px; font-weight: 600; color: var(--ink); }
  .contact-item { display: flex; align-items: center; gap: 6px; }
  .footer { position: absolute; left: 0; top: 976px; width: 680px; height: 38px; background: var(--brand-blue); }
  .social { position: absolute; right: 38px; top: 7px; display: flex; gap: 10px; }
  .social span { width: 25px; height: 25px; border-radius: 50%; border: 1.5px solid #1c3f57; }
</style>
</head>
<body>
<main class="email">
  <header class="header">
    <div class="brand">
      <span class="brand-dot"></span>
      <span class="brand-name">Tarvo Claim Services</span>
    </div>
    <div class="helpline">
      <svg width="14" height="24" viewBox="0 0 14 24"><rect x="1" y="1" width="12" height="22" rx="2" fill="none" stroke="#1f5c85" stroke-width="2"/><circle cx="7" cy="19" r="1.2" fill="#1f5c85"/></svg>
      <div><small>Need Help? Call Us Now</small><strong>16125550148</strong></div>
    </div>
    <a class="cta" href="https://www.tarvoclaimservices.com">GET IN TOUCH
      <svg width="10" height="10" viewBox="0 0 10 10"><circle cx="5" cy="5" r="5" fill="#fff"/><path d="M4 2.8 6.2 5 4 7.2" fill="none" stroke="#2f77a0" stroke-width="1.4"/></svg>
    </a>
  </header>

  <section class="hero">
    <div class="hero-photo" role="img" aria-label="Stock photo of a billing specialist writing notes beside a laptop and a small potted plant"></div>
    <svg class="hero-tint" width="680" height="411" viewBox="0 0 680 411">
      <polygon points="0,0 240,0 380,411 0,411" fill="#5b94bd" opacity="0.55"/>
    </svg>
    <h1 class="hero-title"><span class="line-one">Tarvo Claim</span><span class="line-two">Services</span></h1>
  </section>
  <div class="hero-band"></div>
  <div class="portrait" role="img" aria-label="Circular portrait spot for the sender's photo"></div>

  <h2 class="section-title about-title">About Us</h2>
  <p class="section-text about-text">Ea consul insolens interesset usu, id ius nihil nostrum tacimates. Eu mu alii quando epicurei. Ut eum lorem rationibus. In ius nobis accommoda uat conceptam ei sea, at prompta qualisque corrumpit vel. Nec ea dign et noluisse splendide duo. No ius zril adversarium, cu</p>

  <h2 class="section-title services-title">Our Services</h2>
  <p class="section-text services-text">Ea consul insolens interesset usu, id ius nihil nostrum tacimates. Eu mu eresset usu, id ius nihil nostrum tacimates. Eu mu alii quando epicurei. Ut eum lorem rationibus. In ius nobis accommodaUt eum lorem rationibus. In ius nobis a</p>

  <div class="service-row">
    <div class="service">
      <svg width="28" height="32" viewBox="0 0 28 32"><path d="M3 2h16l6 6v22H3z" fill="none" stroke="#2f77a0" stroke-width="2.4"/><path d="M8 12h12M8 17h12M8 22h9" stroke="#2f77a0" stroke-width="2"/></svg>
      <p>Clean claim filing for every visit, checked and sent the same day.</p>
    </div>
    <div class="service">
      <svg width="30" height="32" viewBox="0 0 30 32"><circle cx="18" cy="11" r="8" fill="none" stroke="#2f77a0" stroke-width="3"/><path d="M12 17 3 28" stroke="#2f77a0" stroke-width="4" stroke-linecap="round"/></svg>
      <p>Denial review that finds lost revenue and fixes coding gaps fast.</p>
    </div>
    <div class="service">
      <svg width="30" height="32" viewBox="0 0 30 32"><circle cx="15" cy="18" r="11" fill="none" stroke="#2f77a0" stroke-width="2.6"/><path d="M12 3h6M15 3v4M15 18V12M15 18l4 3" stroke="#2f77a0" stroke-width="2.4"/></svg>
      <p>Quick turnaround on payments so your cash flow stays steady.</p>
    </div>
    <div class="service">
      <svg width="32" height="30" viewBox="0 0 32 30"><path d="M16 2 2 15h4v13h7v-8h6v8h7V15h4z" fill="#2f77a0"/></svg>
      <p>Remote billing support for practices working from any location.</p>
    </div>
  </div>

  <p class="news-label">REMOTE MEDICAL BILLING WORK ON THE RISE</p>
  <p class="news-text">Remote medical billing work on the rise thanks to COVID-19. Most people are not ready to risk bringing contagion home to their families. Rightfully so, they are choosing to not work at places where there are large crowds or many customers. Preferring smaller less trafficked setting. The trend is only going to continue as new platforms are made available every single week. It has been determined that outsourcing is the way of the future for medical billing. Is your practice on</p>

  <div class="contact">
    <div class="contact-item">
      <svg width="14" height="20" viewBox="0 0 14 20"><path d="M7 1a6 6 0 0 0-6 6c0 5 6 12 6 12s6-7 6-12a6 6 0 0 0-6-6z" fill="#2f77a0"/><circle cx="7" cy="7" r="2.2" fill="#fff"/></svg>
      <span>270 Cedar Ridge Ave Ste 400 Saint<br>Paul, Minnesota 55102</span>
    </div>
    <div class="contact-item">
      <svg width="11" height="20" viewBox="0 0 11 20"><rect x="1" y="1" width="9" height="18" rx="1.5" fill="none" stroke="#2f77a0" stroke-width="1.6"/></svg>
      <span>612-555-0148</span>
    </div>
    <div class="contact-item">
      <svg width="20" height="16" viewBox="0 0 20 16"><rect x="1" y="5" width="18" height="10" rx="1" fill="#2f77a0"/><rect x="5" y="1" width="10" height="5" fill="#2f77a0"/></svg>
      <span>612-555-0148</span>
    </div>
    <div class="contact-item">
      <svg width="18" height="13" viewBox="0 0 18 13"><rect x="1" y="1" width="16" height="11" fill="none" stroke="#2f77a0" stroke-width="1.6"/><path d="M1 1l8 6 8-6" fill="none" stroke="#2f77a0" stroke-width="1.6"/></svg>
      <span>hello@tarvoclaimservices.com</span>
    </div>
  </div>

  <footer class="footer">
    <div class="social" aria-label="Social links"><span></span><span></span><span></span><span></span></div>
  </footer>
</main>
</body>
</html>
```